we can communicate on this, but i want to follow the approach we took on Pellew|Marsh & Quinlan but i feel the card front needs the black background and the platinum and gold logo. The back? I am open. we can use the same info from PM&Q. Velmont Arc is an enhanced equity investment fund - basically a very exclusive boutique hedge fund that uses only stock options. very advanced things. hope you are interested

Contact Information for Business Card

Dr. Lewis T. Brennick, CFA
Scientifique de fusée financière
701.555.0143
LTBquant47@mailvantor.com

4718 Willow Creek Bend W.
West Fargo, ND 58078

No web site

Colors

Designer to choose colors to be used in the design.

Requirements
Nice to have
• I tend to prefer the most visible applications of the logo to include logo and name, the logo version with a black background and the gold and platinum components separated by the black. I see this working well for a single side (logo and name - this is card front to me).
• I am fairly open to other treatments on the reverse side with the data. To me, it makes sense to have a different color rendition of the logo on the reverse and it may be a muted black tone on tone or an oversized portion that would have spot UV. Or, the reverse may play with colors and layout
Should not have
• Other colors = no no
• Decorative font

```html
<!DOCTYPE html>
<html lang="en">
<head>
<meta charset="utf-8">
<title>Velmont Arc – Business Card</title>
<link rel="stylesheet" href="https://fonts.googleapis.com/css2?family=Open+Sans:wght@400;600;700&display=swap">
<style>
  :root {
    --ink: #151416;
    --paper: #ffffff;
    --gold: #cfa94a;
    --stage: #2a2a2c;
  }
  * { box-sizing: border-box; margin: 0; padding: 0; }
  html, body {
    width: 1200px; height: 900px; overflow: hidden;
    background: var(--stage);
    font-family: "Open Sans", Arial, sans-serif;
  }
  .stage {
    position: relative; width: 1200px; height: 900px;
    display: flex; flex-direction: column; align-items: center; justify-content: center; gap: 40px;
  }
  .card {
    position: relative; width: 620px; height: 354px;
    border-radius: 22px; overflow: hidden;
  }

  /* Front */
  .card-front { background: var(--ink); }
  .front-brand {
    position: absolute; inset: 0;
    display: flex; flex-direction: column; align-items: center; justify-content: center; gap: 18px;
  }
  .brand-dot {
    width: 86px; height: 86px; border-radius: 50%;
    background: var(--gold);
  }
  .brand-name {
    font-weight: 700; font-size: 38px; letter-spacing: 2px;
    text-transform: uppercase; color: var(--paper); line-height: 1;
  }

  /* Back */
  .card-back { background: var(--paper); }
  .back-wave { position: absolute; inset: 0; width: 620px; height: 354px; }
  .back-brand {
    position: absolute; right: 34px; top: 44px;
    display: flex; flex-direction: column; align-items: center; gap: 10px;
  }
  .back-brand .brand-dot { width: 62px; height: 62px; }
  .back-brand .brand-name { color: var(--ink); font-size: 28px; }

  .holder { position: absolute; left: 40px; top: 184px; }
  .holder-name {
    font-weight: 700; font-size: 23px; color: var(--gold);
    text-transform: uppercase; letter-spacing: 0.5px; line-height: 1.1;
  }
  .holder-role { font-weight: 600; font-size: 15px; color: var(--paper); margin-top: 3px; }

  .contact-list { list-style: none; position: absolute; left: 40px; top: 252px; }
  .contact-list li {
    display: flex; align-items: center; gap: 9px;
    font-size: 13.5px; color: var(--paper); line-height: 22px;
  }
  .contact-list svg { width: 13px; height: 13px; fill: var(--gold); flex: none; }

  .address {
    position: absolute; right: 40px; bottom: 18px;
    text-align: right; font-size: 14px; color: var(--paper); line-height: 1.4;
  }
</style>
</head>
<body>
<main class="stage">

  <section class="card card-front" aria-label="Card front">
    <div class="front-brand">
      <span class="brand-dot"></span>
      <span class="brand-name">Velmont Arc</span>
    </div>
  </section>

  <section class="card card-back" aria-label="Card back">
    <svg class="back-wave" viewBox="0 0 620 354" aria-hidden="true">
      <path fill="var(--gold)" d="M0,136 C180,126 260,156 360,216 C440,264 530,278 620,266 L620,354 L0,354 Z"/>
      <path fill="var(--paper)" d="M0,142 C180,132 260,162 360,222 C440,270 530,284 620,272 L620,354 L0,354 Z"/>
      <path fill="var(--ink)" d="M0,150 C180,140 260,170 360,230 C440,278 530,292 620,280 L620,354 L0,354 Z"/>
    </svg>

    <div class="back-brand">
      <span class="brand-dot"></span>
      <span class="brand-name">Velmont Arc</span>
    </div>

    <div class="holder">
      <p class="holder-name">Tobin Harlowe</p>
      <p class="holder-role">Doctor</p>
    </div>

    <ul class="contact-list">
      <li>
        <svg viewBox="0 0 24 24" aria-hidden="true"><path d="M6.6 10.8a15.1 15.1 0 0 0 6.6 6.6l2.2-2.2a1 1 0 0 1 1-.25 11.4 11.4 0 0 0 3.6.57 1 1 0 0 1 1 1V20a1 1 0 0 1-1 1A17 17 0 0 1 3 4a1 1 0 0 1 1-1h3.5a1 1 0 0 1 1 1c0 1.25.2 2.45.57 3.6a1 1 0 0 1-.25 1z"/></svg>
        216-555-0187
      </li>
      <li>
        <svg viewBox="0 0 24 24" aria-hidden="true"><path d="M2 5h20v14H2zm2 2v.4l8 5.2 8-5.2V7zm0 2.8V17h16V9.8l-8 5.2z"/></svg>
        info@quillmarsh.com.au
      </li>
      <li>
        <svg viewBox="0 0 24 24" aria-hidden="true"><circle cx="12" cy="12" r="10"/></svg>
        www.quillmarsh.com.au
      </li>
    </ul>

    <p class="address">Street Name loc, Ardenvale<br>Corliss stand, 20417</p>
  </section>

</main>
</body>
</html>
```